Packaging Design: Logo/Bottle Design for New Botanical Cocktail Brand

We are a new start up, looking to create a new line of Ready to drink Cocktails. The brand name is Verdance Garden Spritzers, infused with fruit, herb, and floral botanicals grown on our farm in New Hampshire. Flavors will include: Herb flavored with cilantro, Berry- flavored with Ridgeglow Berry, Citrus flavored with lemon Verbena & lemon balm, Pear flavored with Quillon pear, Cucumber & Mint. We need a logo and a label design. There are 2 possible bottles to choose from.

Designer has complete freedom with everything! From fonts and colors to bottle caps and closures. Please view the pinterest link for inspirational bottle designs. https://www.pinboardia.com/dellacravitz/garden-spritzers/

Reason: I am extending the deadline for my project to allow more designers to submit their designs.

Target Market(s)

Female 21 to 48 years old. College educated and professional. The type of person that has a passion for a cause and eats and shops local. People that respect an artisan quality product, hand made by a master craftsman.

Industry/Entity Type

Floral

Requirements
Must have
• Clear Bottle, see options attached. You may also choose your own BUT WE MUST SEE THE LOGO AND IMAGERY ON A BOTTLE
• Logo Design: "Verdance Garden Spritzers"
• Label: We can have front and back, or one continuous label. We are open to painted designs.
• The label must contain the following text in quotes:
• Product Name: " Verdance Garden Spritzers "
• "15% Alc. by Vol. (30 proof)"
• "750 mL"
• "Handcrafted and Bottled by Hollowmere Stillbrook Farm and Distillery
• Winchester, NH-USA"
• The following Text must be in all caps and 3mm in height:
• "Government Warning: (1) According to the Surgeon General, women should not drink alcoholic beverages during pregnancy because of the risk of birth defects. (2) Consumption of alcoholic beverages impairs your ability to drive a car or operate machinery and may cause health problems."
• Must be a space for a bar code: .75 in height by 1.25 in length.
• “www.hollowmerestillbrook.com”
• Must Have the following Statement:
• Infused with fruit, herb, and floral botanicals and sweetened with stevia. Serve cold over ice.
Nice to have
• Antique or vintage botanical illustrations
• https://www.pinboardia.com/dellacravitz/garden-spritzers/
• check out the board for inspiration.
• Think artisanal small batch spirits that are ready to drink out of the bottle. Refreshing flavors just pour over ice and add herb leaves.
• You can use images by doing a search here.
• http://archv.plantrec.example.org/archv/search.xhtml?start=0&collectionFacet=Orchard+Painted+Plate+Archive

```html
<!DOCTYPE html>
<html lang="en">
<head>
<meta charset="utf-8">
<title>Verdance Garden Spritzers – Label Range</title>
<link rel="stylesheet" href="https://fonts.googleapis.com/css2?family=Poiret+One&family=Josefin+Sans:wght@400&display=swap">
<style>
  :root {
    --backdrop: #e4e2df;
    --label-paper: #f6f4ef;
    --label-rule: #c9c6c0;
    --neck-gold: #f1c98a;
    --neck-gold-deep: #e6b46c;
    --brand-rose: #a47c6c;
    --ink: #2a2624;
    --berry-red: #d9553f;
    --citrus-orange: #d98a3a;
    --pear-gold: #cfa349;
    --leaf-green: #6e8a52;
  }
  * { box-sizing: border-box; margin: 0; padding: 0; }
  html, body {
    width: 1200px;
    height: 966px;
    overflow: hidden;
    background: var(--backdrop);
  }
  .range {
    position: relative;
    width: 1200px;
    height: 966px;
    display: flex;
    justify-content: space-between;
    padding: 0 38px;
  }
  .flavour {
    position: relative;
    width: 330px;
    height: 966px;
  }
  .neck-label {
    position: absolute;
    left: 122px;
    top: 118px;
    width: 86px;
    height: 182px;
    background: linear-gradient(to bottom, var(--neck-gold), var(--neck-gold-deep));
    display: flex;
    align-items: flex-start;
    justify-content: center;
    padding-top: 54px;
  }
  .neck-label .brand-name {
    font-family: "Poiret One", sans-serif;
    font-size: 17px;
    color: var(--brand-rose);
    letter-spacing: 0.5px;
  }
  .body-label {
    position: absolute;
    left: 50px;
    top: 388px;
    width: 232px;
    height: 388px;
    background: var(--label-paper);
    border-top: 1px solid var(--label-rule);
    border-bottom: 1px solid var(--label-rule);
  }
  .section-rule {
    position: absolute;
    left: 0;
    width: 100%;
    height: 1px;
    background: var(--label-rule);
  }
  .section-rule.upper { top: 138px; }
  .section-rule.lower { top: 290px; }
  .flavour-name {
    position: absolute;
    top: 8px;
    width: 100%;
    text-align: center;
    font-family: "Josefin Sans", sans-serif;
    font-size: 16px;
    letter-spacing: 1px;
    color: var(--ink);
  }
  .flavour-name.wide { letter-spacing: 3px; }
  .illustration {
    position: absolute;
    left: 46px;
    top: 34px;
    width: 140px;
    height: 130px;
  }
  .brand-mark {
    position: absolute;
    top: 186px;
    width: 100%;
    text-align: center;
    font-family: "Poiret One", sans-serif;
    font-size: 40px;
    color: var(--brand-rose);
  }
  .brand-line {
    position: absolute;
    left: 24px;
    top: 294px;
    width: 184px;
    height: 86px;
    border: 1px solid #e2ded8;
    display: flex;
    flex-direction: column;
    justify-content: center;
    align-items: center;
    gap: 2px;
    font-family: "Poiret One", sans-serif;
    font-size: 19px;
    letter-spacing: 2px;
    color: var(--brand-rose);
    line-height: 1.1;
  }
</style>
</head>
<body>
<main class="range">

  <section class="flavour">
    <div class="neck-label"><span class="brand-name">Verdance</span></div>
    <div class="body-label">
      <div class="section-rule upper"></div>
      <div class="section-rule lower"></div>
      <h2 class="flavour-name">BERRY</h2>
      <svg class="illustration" viewBox="0 0 140 130" role="img" aria-label="Vintage botanical illustration of red berries with leaves and a white blossom">
        <defs>
          <radialGradient id="berry-tone" cx="40%" cy="45%" r="65%">
            <stop offset="0" stop-color="#e8765f"/>
            <stop offset="0.6" stop-color="var(--berry-red)"/>
            <stop offset="1" stop-color="#7f9a62"/>
          </radialGradient>
        </defs>
        <rect width="140" height="130" rx="30" fill="url(#berry-tone)" opacity="0.85"/>
      </svg>
      <div class="brand-mark">Verdance</div>
      <div class="brand-line"><span>VERDANCE</span><span>GARDEN</span><span>SPRITZERS</span></div>
    </div>
  </section>

  <section class="flavour">
    <div class="neck-label"><span class="brand-name">Verdance</span></div>
    <div class="body-label">
      <div class="section-rule upper"></div>
      <div class="section-rule lower"></div>
      <h2 class="flavour-name">CITRUS</h2>
      <svg class="illustration" viewBox="0 0 140 130" role="img" aria-label="Vintage botanical illustration of an orange and a lemon on a leafy branch">
        <defs>
          <radialGradient id="citrus-tone" cx="40%" cy="60%" r="65%">
            <stop offset="0" stop-color="#e8843a"/>
            <stop offset="0.5" stop-color="#d9c25a"/>
            <stop offset="1" stop-color="var(--leaf-green)"/>
          </radialGradient>
        </defs>
        <rect width="140" height="130" rx="30" fill="url(#citrus-tone)" opacity="0.85"/>
      </svg>
      <div class="brand-mark">Verdance</div>
      <div class="brand-line"><span>VERDANCE</span><span>GARDEN</span><span>SPRITZERS</span></div>
    </div>
  </section>

  <section class="flavour">
    <div class="neck-label"><span class="brand-name">Verdance</span></div>
    <div class="body-label">
      <div class="section-rule upper"></div>
      <div class="section-rule lower"></div>
      <h2 class="flavour-name wide">PEAR</h2>
      <svg class="illustration" viewBox="0 0 140 130" role="img" aria-label="Vintage botanical illustration of a golden pear with leaves">
        <defs>
          <radialGradient id="pear-tone" cx="45%" cy="55%" r="65%">
            <stop offset="0" stop-color="#e6c068"/>
            <stop offset="0.55" stop-color="var(--pear-gold)"/>
            <stop offset="1" stop-color="#5f7448"/>
          </radialGradient>
        </defs>
        <rect width="140" height="130" rx="30" fill="url(#pear-tone)" opacity="0.85"/>
      </svg>
      <div class="brand-mark">Verdance</div>
      <div class="brand-line"><span>VERDANCE</span><span>GARDEN</span><span>SPRITZERS</span></div>
    </div>
  </section>

</main>
</body>
</html>
```